A5 Flyer for Financial Services Business

I am after a re-design of our business flyer to fit in with our new branding style and logo colour scheme. Wanting something with a bit of designer flair that I could not create myself. I have included the flyer which I created which lacks style so dazzle me.

I want to use the same content.

Text for main body of flyer is

Are you a small business owner, tradie or TRPQ Service Provider struggling to stay on top of your bookkeeping and compliance obligations? If so we would love to help you get back on track and take control of your business finances so that you can make informed business decisions and focus on what you do best.

We have over 20 years industry experience and, as a small business ourselves, we are able to offer our clients a personal bookkeeping solution tailored to meet the needs of your business.

Accounts Payable | Accounts Receivable
Customer Invoicing
Bank and Credit Card Reconciliations
Payroll | Superannuation | Payroll Tax
Business Activity | Instalment Activity Statements
Regular Financial Reports
Vantly and Brimfolk Set-Up and Training

```html
<!DOCTYPE html>
<html lang="en">
<head>
<meta charset="utf-8">
<title>Even Keel Financial Services – Bookkeeping Flyer</title>
<link rel="stylesheet" href="https://fonts.googleapis.com/css2?family=Bebas+Neue&family=Roboto:wght@400;700&family=Montserrat:wght@300;400;500;600&family=Poppins:wght@400;600;700&display=swap">
<style>
  :root {
    --teal: #0f9690;
    --teal-bright: #16b3aa;
    --teal-deep: #0b5878;
    --grey: #6d6e70;
    --charcoal: #3e3f41;
    --ink: #2b2b2d;
    --badge: #e2e6e6;
    --badge-edge: #c6cdcd;
    --paper: #ffffff;
  }
  * { box-sizing: border-box; margin: 0; padding: 0; }
  html, body { width: 783px; height: 1200px; overflow: hidden; background: var(--paper); }
  .flyer { position: relative; width: 783px; height: 1200px; background: var(--paper); font-family: "Montserrat", sans-serif; color: var(--ink); }
  .header-art { position: absolute; left: 0; top: 0; }

  .brand { position: absolute; left: 56px; top: 62px; width: 300px; text-align: center; color: var(--teal); font-family: "Montserrat", sans-serif; font-weight: 300; }
  .brand-dot { width: 64px; height: 64px; border-radius: 50%; background: var(--teal); margin: 0 auto 14px; }
  .brand-name { font-size: 28px; letter-spacing: 0.5px; line-height: 1.1; }
  .brand-sub { font-size: 14px; letter-spacing: 6px; line-height: 1.4; }

  .headline { position: absolute; left: 56px; top: 250px; color: var(--paper); line-height: 1; }
  .headline span { display: block; }
  .headline .hl-main { font-family: "Bebas Neue", sans-serif; font-size: 74px; line-height: 62px; letter-spacing: 0.5px; }
  .headline .hl-bold { font-family: "Roboto", sans-serif; font-weight: 700; font-size: 48px; line-height: 46px; }
  .headline .hl-light { font-family: "Roboto", sans-serif; font-weight: 400; font-size: 46px; line-height: 42px; }
  .headline .hl-last { font-family: "Roboto", sans-serif; font-weight: 700; font-size: 40px; line-height: 44px; }

  .intro { position: absolute; left: 52px; top: 548px; width: 312px; font-size: 13.4px; line-height: 19.4px; text-align: justify; letter-spacing: -0.1px; }
  .intro-more { position: absolute; left: 200px; top: 724px; width: 164px; font-size: 13.4px; line-height: 19.3px; letter-spacing: -0.1px; }

  .seal { position: absolute; left: 55px; top: 734px; }

  .team-photo { position: absolute; left: 52px; top: 899px; width: 310px; height: 160px; background: linear-gradient(135deg, #e9eef1 0%, #b9c4cc 55%, #5d6670 100%); clip-path: polygon(0 0, 93% 0, 100% 12%, 100% 100%, 6% 100%, 0 88%); }

  .services-title { position: absolute; left: 427px; top: 550px; font-family: "Montserrat", sans-serif; font-size: 25px; font-weight: 400; color: var(--ink); }
  .services-title strong { font-weight: 600; }
  .services-box { position: absolute; left: 420px; top: 589px; width: 316px; height: 385px; border-radius: 11px; background: linear-gradient(180deg, var(--teal) 0%, var(--teal-deep) 100%); border: 3px solid #fff; box-shadow: 0 0 0 1px #d9dede, 0 3px 8px rgba(0,0,0,.2); }
  .service-list { list-style: none; position: absolute; left: 26px; top: 28px; color: #fff; font-family: "Poppins", sans-serif; font-weight: 600; font-size: 14.5px; line-height: 15px; }
  .service-list li { position: relative; padding-left: 22px; margin-bottom: 15.5px; }
  .service-list li svg { position: absolute; left: 0; top: 1px; }

  .partner-row { position: absolute; left: 420px; top: 994px; }

  .contact-web { position: absolute; left: 56px; top: 1106px; font-family: "Poppins", sans-serif; font-weight: 600; font-size: 12.5px; color: var(--ink); }
  .contact-web p { display: flex; align-items: center; gap: 8px; height: 23px; }

  .footer-band { position: absolute; left: 0; top: 1076px; }
  .call { position: absolute; left: 448px; top: 1101px; font-family: "Poppins", sans-serif; font-weight: 600; font-size: 21px; color: #fff; white-space: nowrap; }
  .call .call-label { color: var(--teal-bright); }
  .postal { position: absolute; left: 448px; top: 1139px; font-family: "Poppins", sans-serif; font-weight: 600; font-size: 15px; color: #fff; display: flex; align-items: center; gap: 8px; }
</style>
</head>
<body>
<div class="flyer">

  <svg class="header-art" width="783" height="522" viewBox="0 0 783 522">
    <defs>
      <linearGradient id="tealFade" x1="0" y1="0" x2="0" y2="1">
        <stop offset="0" stop-color="#0f9690"/>
        <stop offset="1" stop-color="#0b5878"/>
      </linearGradient>
      <linearGradient id="officeTones" x1="0" y1="0" x2="1" y2="1">
        <stop offset="0" stop-color="#3a3b3d"/>
        <stop offset="0.5" stop-color="#6b6a68"/>
        <stop offset="1" stop-color="#1f2022"/>
      </linearGradient>
    </defs>
    <polygon points="470,0 503,0 362,250 346,226" fill="var(--grey)"/>
    <polygon points="0,207 336,207 490,474 287,474 243,522 0,522" fill="url(#tealFade)"/>
    <polygon points="295,481 783,481 783,522 253,522" fill="var(--grey)"/>
    <polygon points="520,0 783,0 783,474 497,474 374,260" fill="url(#officeTones)" role="img" aria-label="Photo of a businesswoman in glasses reviewing financial charts at her desk"/>
  </svg>

  <div class="brand">
    <div class="brand-dot"></div>
    <div class="brand-name">EVEN KEEL</div>
    <div class="brand-sub">Financial Services</div>
  </div>

  <h1 class="headline">
    <span class="hl-main">BOOKKEEPING</span>
    <span class="hl-bold">TAILORED</span>
    <span class="hl-light">TO YOUR</span>
    <span class="hl-last">BUSINESS NEEDS</span>
  </h1>

  <p class="intro">Are you a small business owner, tradie or TRPQ Service Provider struggling to stay on top of your bookkeeping and compliance obligations? If so we would love to help you get back on track and take control of your business finances so that you can make informed business decisions and focus on what you do best.</p>

  <svg class="seal" width="132" height="132" viewBox="0 0 132 132">
    <circle cx="66" cy="66" r="64" fill="var(--teal)" stroke="var(--teal-deep)" stroke-width="3" stroke-dasharray="6 3"/>
    <circle cx="66" cy="66" r="50" fill="#e9ecec" stroke="#fff" stroke-width="3"/>
    <text x="66" y="44" text-anchor="middle" font-family="Montserrat, sans-serif" font-size="12" fill="#333">We have</text>
    <text x="66" y="55" text-anchor="middle" font-family="Montserrat, sans-serif" font-size="12" fill="#333">over</text>
    <text x="66" y="82" text-anchor="middle" font-family="Bebas Neue, sans-serif" font-size="32" fill="var(--teal-deep)">20 YEARS</text>
    <text x="66" y="93" text-anchor="middle" font-family="Montserrat, sans-serif" font-weight="500" font-size="8.5" fill="#333">INDUSTRY</text>
    <text x="66" y="103" text-anchor="middle" font-family="Montserrat, sans-serif" font-weight="500" font-size="8.5" fill="#333">EXPERIENCE</text>
  </svg>

  <p class="intro-more">And as a small business ourselves, we are able to offer our clients a personal bookkeeping solution tailored to meet the needs of your business.</p>

  <div class="team-photo" role="img" aria-label="Photo of a woman presenting a bar chart to colleagues in a meeting room"></div>

  <h2 class="services-title">OUR <strong>SERVICES</strong></h2>
  <div class="services-box">
    <ul class="service-list">
      <li><svg width="12" height="12" viewBox="0 0 12 12"><circle cx="6" cy="6" r="6" fill="var(--teal-bright)"/><path d="M3.2 6.2 5.2 8 8.8 4.2" stroke="#fff" stroke-width="1.6" fill="none"/></svg>Accounts Payable<br>Accounts Receivable</li>
      <li><svg width="12" height="12" viewBox="0 0 12 12"><circle cx="6" cy="6" r="6" fill="var(--teal-bright)"/><path d="M3.2 6.2 5.2 8 8.8 4.2" stroke="#fff" stroke-width="1.6" fill="none"/></svg>Customer Invoicing</li>
      <li><svg width="12" height="12" viewBox="0 0 12 12"><circle cx="6" cy="6" r="6" fill="var(--teal-bright)"/><path d="M3.2 6.2 5.2 8 8.8 4.2" stroke="#fff" stroke-width="1.6" fill="none"/></svg>Bank and Credit Card<br>Reconciliations</li>
      <li><svg width="12" height="12" viewBox="0 0 12 12"><circle cx="6" cy="6" r="6" fill="var(--teal-bright)"/><path d="M3.2 6.2 5.2 8 8.8 4.2" stroke="#fff" stroke-width="1.6" fill="none"/></svg>Payroll</li>
      <li><svg width="12" height="12" viewBox="0 0 12 12"><circle cx="6" cy="6" r="6" fill="var(--teal-bright)"/><path d="M3.2 6.2 5.2 8 8.8 4.2" stroke="#fff" stroke-width="1.6" fill="none"/></svg>Superannuation</li>
      <li><svg width="12" height="12" viewBox="0 0 12 12"><circle cx="6" cy="6" r="6" fill="var(--teal-bright)"/><path d="M3.2 6.2 5.2 8 8.8 4.2" stroke="#fff" stroke-width="1.6" fill="none"/></svg>Payroll Tax</li>
      <li><svg width="12" height="12" viewBox="0 0 12 12"><circle cx="6" cy="6" r="6" fill="var(--teal-bright)"/><path d="M3.2 6.2 5.2 8 8.8 4.2" stroke="#fff" stroke-width="1.6" fill="none"/></svg>Business Activity</li>
      <li><svg width="12" height="12" viewBox="0 0 12 12"><circle cx="6" cy="6" r="6" fill="var(--teal-bright)"/><path d="M3.2 6.2 5.2 8 8.8 4.2" stroke="#fff" stroke-width="1.6" fill="none"/></svg>Instalment Activity Statements</li>
      <li><svg width="12" height="12" viewBox="0 0 12 12"><circle cx="6" cy="6" r="6" fill="var(--teal-bright)"/><path d="M3.2 6.2 5.2 8 8.8 4.2" stroke="#fff" stroke-width="1.6" fill="none"/></svg>Regular Financial Reports</li>
      <li><svg width="12" height="12" viewBox="0 0 12 12"><circle cx="6" cy="6" r="6" fill="var(--teal-bright)"/><path d="M3.2 6.2 5.2 8 8.8 4.2" stroke="#fff" stroke-width="1.6" fill="none"/></svg>Vantly and Brimfolk<br>Set-Up and Training</li>
    </ul>
  </div>

  <svg class="partner-row" width="320" height="64" viewBox="0 0 320 64" role="img" aria-label="Partner and certification badges">
    <circle cx="30" cy="30" r="27" fill="var(--badge)" stroke="var(--badge-edge)" stroke-width="1.5"/>
    <circle cx="94" cy="30" r="27" fill="var(--badge)" stroke="var(--badge-edge)" stroke-width="1.5"/>
    <circle cx="158" cy="30" r="27" fill="var(--badge)" stroke="var(--badge-edge)" stroke-width="1.5"/>
    <circle cx="222" cy="30" r="27" fill="var(--badge)" stroke="var(--badge-edge)" stroke-width="1.5"/>
    <circle cx="286" cy="30" r="27" fill="var(--badge)" stroke="var(--badge-edge)" stroke-width="1.5"/>
  </svg>

  <svg class="footer-band" width="783" height="124" viewBox="0 0 783 124">
    <polygon points="423,0 432,0 372,101 363,101" fill="var(--teal)"/>
    <polygon points="450,0 783,0 783,101 390,101" fill="var(--charcoal)"/>
    <rect x="0" y="101" width="783" height="23" fill="var(--charcoal)"/>
  </svg>

  <div class="contact-web">
    <p><svg width="16" height="12" viewBox="0 0 16 12"><rect x="0.5" y="0.5" width="15" height="11" fill="var(--teal)"/><path d="M0.5 0.5 8 7 15.5 0.5" stroke="#fff" stroke-width="1.2" fill="none"/></svg>info@evenkeelfinancial.com.au</p>
    <p><svg width="16" height="16" viewBox="0 0 16 16"><circle cx="8" cy="8" r="7" fill="none" stroke="var(--teal)" stroke-width="1.5"/><ellipse cx="8" cy="8" rx="3" ry="7" fill="none" stroke="var(--teal)" stroke-width="1.2"/><path d="M1 8 H15 M2.5 4.5 H13.5 M2.5 11.5 H13.5" stroke="var(--teal)" stroke-width="1.2"/></svg>www.evenkeelfinancial.com.au</p>
  </div>

  <p class="call"><span class="call-label">CALL US NOW:</span> 0400 172 358</p>
  <p class="postal"><svg width="13" height="18" viewBox="0 0 13 18"><path d="M6.5 0 C2.9 0 0 2.9 0 6.5 C0 11 6.5 18 6.5 18 S13 11 13 6.5 C13 2.9 10.1 0 6.5 0 Z" fill="var(--teal-bright)"/><circle cx="6.5" cy="6.5" r="2.4" fill="var(--charcoal)"/></svg>PO Box 27 Harlow Bay NSW 2999</p>

</div>
</body>
</html>
```